International Film making Business needs the 5 Logos provided made into a POSTER Format

Design Task:
CREATE A POSTER DESIGN USING THE 5 LOGOS PROVIDED. The BOLD BRIGHT HORIZON LOGO should stand out from the others by being in the middle with the other 4 logos connected to it somehow.

The 5 Businesses already has their 5 Logos, all similar in design to each other.

BOLD BRIGHT HORIZON is the Main Logo that encompasses the other 4 Logos. So it must stand out more and it is like the Overall Business entity that incorporates the other 4 Logos.

What is required is that by using the 5 Logo designs provided, create a cool graphic artwork that somehow incorporates ALL of the 5 Logos - But having the BOLD BRIGHT HORIZON Logo at the forefront/most important/standing out the most.
- BOLD BRIGHT HORIZON will probably be bigger than the others
- and could be changed into 3D.

I have attached all 5 logos and a hand drawn example of how the VARO LUNE ASCENT could stand out from the rest.

THE DESIGNS OF THE LOGOS SHOULD NOT BE CHANGED (except the BOLDBRIGHTHORIZON which can be 3D)

Please do not be restricted with the sample idea. Creativity is encouraged

DIMENSION: 3000 mm x 6000 mm
high resolution graphic

Logo Text

bold bright , bold bright pictures, bold bright legends, bold bright groovy, VARO LUNE ASCENT

Requirements
Must have
• USE THE 5 LOGOS PROVIDED ONLY - Only BOLD BRIGHT HORIZON can be changed into 3D only
Nice to have
• Eye catching design, showing the Bold Bright Horizon as the most powerful Logo that has the other 4 as subordinate companies
Should not have
• ANY CHANGE IN THE 5 LOGO DESIGNS (EXcept 3D for Bold Bright Horizons)

```html
<!DOCTYPE html>
<html lang="en">
<head>
<meta charset="utf-8">
<title>Varo Lune Ascent – Poster</title>
<link rel="stylesheet" href="https://fonts.googleapis.com/css2?family=Cinzel:wght@600&family=Questrial&display=swap">
<style>
  :root {
    --gold: #c9a24a;
    --black: #000000;
    --silver: #dfe3e8;
    --grey-text: #9a9b9e;
    --ink: #151515;
    --white-soft: #fbfbf6;
    --forest: #0c5330;
  }
  html, body {
    margin: 0;
    padding: 0;
    width: 1200px;
    height: 600px;
    overflow: hidden;
    background: var(--black);
  }
  .poster { display: block; width: 1200px; height: 600px; }
  .brand-name { font-family: "Cinzel", serif; font-weight: 600; }
  .main-name, .main-mark { fill: var(--gold); }
  .web-address { font-family: "Questrial", sans-serif; fill: var(--grey-text); }
  .frame-inner { fill: var(--black); }
  .name-orbitless, .mark-orbitless { fill: var(--silver); }
  .name-orbit, .mark-orbit { fill: var(--ink); }
  .name-prisma, .mark-prisma { fill: var(--white-soft); }
  .name-cadenza, .mark-cadenza { fill: var(--forest); }
</style>
</head>
<body>
<svg class="poster" viewBox="0 0 1200 600" xmlns="http://www.w3.org/2000/svg">
  <defs>
    <linearGradient id="gold-sheen" x1="0" y1="0" x2="1" y2="0">
      <stop offset="0" stop-color="#b5822c"/>
      <stop offset="0.55" stop-color="#f6e9a8"/>
      <stop offset="1" stop-color="#b07a2a"/>
    </linearGradient>
    <linearGradient id="gold-bevel" x1="0" y1="0" x2="1" y2="1">
      <stop offset="0" stop-color="#b5832a"/>
      <stop offset="0.45" stop-color="#f7e9aa"/>
      <stop offset="1" stop-color="#a8772a"/>
    </linearGradient>
    <linearGradient id="fill-blue" x1="0" y1="1" x2="1" y2="0">
      <stop offset="0" stop-color="#2a4ea2"/>
      <stop offset="0.5" stop-color="#1b78bb"/>
      <stop offset="1" stop-color="#1aa6de"/>
    </linearGradient>
    <linearGradient id="fill-silver" x1="0" y1="0" x2="1" y2="0">
      <stop offset="0" stop-color="#0e0e0e"/>
      <stop offset="0.4" stop-color="#8a8b8e"/>
      <stop offset="0.7" stop-color="#a3a4a7"/>
      <stop offset="1" stop-color="#6b6c6f"/>
    </linearGradient>
    <linearGradient id="fill-spectrum" x1="0" y1="0" x2="1" y2="0">
      <stop offset="0" stop-color="#5a2a8c"/>
      <stop offset="0.2" stop-color="#2b2f86"/>
      <stop offset="0.45" stop-color="#1fa5df"/>
      <stop offset="0.62" stop-color="#2bb58a"/>
      <stop offset="0.82" stop-color="#f2ea1a"/>
      <stop offset="1" stop-color="#f07a1e"/>
    </linearGradient>
    <linearGradient id="fill-green" x1="0" y1="0" x2="1" y2="0">
      <stop offset="0" stop-color="#0a5a48"/>
      <stop offset="0.5" stop-color="#05a24c"/>
      <stop offset="1" stop-color="#55c04a"/>
    </linearGradient>
  </defs>

  <rect class="frame-outer" x="0" y="0" width="1200" height="600" fill="url(#gold-sheen)"/>
  <rect class="frame-inner" x="18" y="18" width="1164" height="564"/>

  <g class="main-lockup">
    <circle class="main-mark" cx="390" cy="150" r="88"/>
    <text class="brand-name main-name" x="524" y="162" font-size="74" textLength="384" lengthAdjust="spacingAndGlyphs">VARO LUNE</text>
    <text class="brand-name main-name" x="524" y="231" font-size="74" textLength="384" lengthAdjust="spacingAndGlyphs">ASCENT</text>
    <text class="web-address" x="524" y="263" font-size="26" textLength="384" lengthAdjust="spacingAndGlyphs">varoluneascent.example</text>
  </g>

  <g class="division division-lune">
    <polygon points="182,283 330,431 182,579 34,431" fill="url(#gold-bevel)"/>
    <polygon points="182,301 312,431 182,561 52,431" fill="url(#fill-blue)"/>
    <circle class="mark-orbitless" cx="126" cy="428" r="24"/>
    <text class="brand-name name-orbitless" x="170" y="428" font-size="34" textLength="100" lengthAdjust="spacingAndGlyphs">VARO</text>
    <text class="brand-name name-orbitless" x="172" y="461" font-size="34" textLength="90" lengthAdjust="spacingAndGlyphs">LUNE</text>
  </g>

  <g class="division division-orbit">
    <polygon points="460,283 608,431 460,579 312,431" fill="url(#gold-bevel)"/>
    <polygon points="460,301 590,431 460,561 330,431" fill="url(#fill-silver)"/>
    <circle class="mark-orbit" cx="394" cy="430" r="24"/>
    <text class="brand-name name-orbit" x="435" y="421" font-size="22" textLength="115" lengthAdjust="spacingAndGlyphs">VARO LUNE</text>
    <text class="brand-name name-orbit" x="433" y="454" font-size="34" textLength="119" lengthAdjust="spacingAndGlyphs">ORBIT</text>
  </g>

  <g class="division division-prisma">
    <polygon points="739,283 887,431 739,579 591,431" fill="url(#gold-bevel)"/>
    <polygon points="739,301 869,431 739,561 609,431" fill="url(#fill-spectrum)"/>
    <circle class="mark-prisma" cx="668" cy="430" r="24"/>
    <text class="brand-name name-prisma" x="703" y="424" font-size="24" textLength="131" lengthAdjust="spacingAndGlyphs">VARO LUNE</text>
    <text class="brand-name name-prisma" x="703" y="451" font-size="28" textLength="131" lengthAdjust="spacingAndGlyphs">PRISMA</text>
  </g>

  <g class="division division-cadenza">
    <polygon points="1018,283 1166,431 1018,579 870,431" fill="url(#gold-bevel)"/>
    <polygon points="1018,301 1148,431 1018,561 888,431" fill="url(#fill-green)"/>
    <circle class="mark-cadenza" cx="1016" cy="396" r="24"/>
    <text class="brand-name name-cadenza" x="1019" y="461" font-size="26" text-anchor="middle" textLength="138" lengthAdjust="spacingAndGlyphs">VARO LUNE</text>
    <text class="brand-name name-cadenza" x="1019" y="491" font-size="32" text-anchor="middle" textLength="138" lengthAdjust="spacingAndGlyphs">CADENZA</text>
  </g>
</svg>
</body>
</html>
```